LEARN Business Skills so you can Earn a good living

size of the poster is 8”x 10.75" plus 0.25" bleed.
Please leave 1 inch on the bottoum for footer
I want a design a poster that will attract people's attention.
I appreciate a creative ad however the ad should not take away from being able to clearly read the text.
-I also appreciate a simple creative ad that is not too busy.
-you can use graphics, vectors, or pictures of real people.
-however, if you use real people it should be a white male that is wearing a white shirt and look like a professional person.

Target Market(s)

Potential young business people

Industry/Entity Type

education

Requirements
Must have
• easy to read the text
Nice to have
• I would like a "creative" simple ad that is easy to be read
Should not have
• pictures of women

```html
<!DOCTYPE html>
<html lang="en">
<head>
<meta charset="utf-8">
<title>Learn It to Earn It — Business Enrichment Course</title>
<link href="https://fonts.googleapis.com/css2?family=Montserrat:wght@400;600;700;800&family=Dancing+Script:wght@600&display=swap" rel="stylesheet">
<style>
  :root{
    --stage:#8f8f8f;
    --band-top:#4e4e5e;
    --band-top-dark:#353540;
    --panel:#414150;
    --panel-dark:#2f2f3a;
    --ghost:rgba(0,0,0,0.16);
    --ink:#ffffff;
    --footer:#ffffff;
    --photo-a:#e9e9ec;
    --photo-b:#8d8e96;
  }
  *{margin:0;padding:0;box-sizing:border-box;}
  html,body{width:1200px;height:1200px;overflow:hidden;background:var(--stage);}
  .poster{
    position:absolute;left:207px;top:80px;width:786px;height:1041px;overflow:hidden;
    background:linear-gradient(160deg,var(--panel) 0%,var(--panel) 55%,var(--panel-dark) 100%);
    font-family:"Montserrat",sans-serif;color:var(--ink);
  }
  .hero-band{
    position:absolute;left:0;top:0;width:786px;height:492px;
    background:linear-gradient(100deg,var(--band-top-dark) 0%,var(--band-top) 60%,#5a5a6a 100%);
  }
  .ghost-word{
    position:absolute;left:12px;font-weight:800;font-size:280px;line-height:1;
    color:var(--ghost);letter-spacing:-6px;white-space:nowrap;
  }
  .ghost-word.top{top:-110px;}
  .ghost-word.bottom{top:200px;}
  .hero-photo{
    position:absolute;left:250px;top:0;width:400px;height:492px;
    background:radial-gradient(ellipse at 60% 45%,var(--photo-a) 0%,#c9c9cf 45%,var(--photo-b) 100%);
    border-radius:120px 120px 0 0;
  }
  .headline{
    position:absolute;left:0;top:0;font-weight:800;line-height:1;
    text-shadow:0 8px 18px rgba(0,0,0,0.35);white-space:nowrap;
  }
  .headline .line{position:absolute;font-size:134px;letter-spacing:-2px;}
  .headline .learn{left:80px;top:353px;}
  .headline .earn{left:160px;top:472px;}
  .headline .joiner{
    position:absolute;left:74px;top:490px;font-family:"Dancing Script",cursive;
    font-weight:600;font-size:120px;letter-spacing:-3px;
  }
  .course{position:absolute;left:72px;top:630px;width:300px;}
  .course h2{font-weight:700;font-size:44px;line-height:42px;letter-spacing:-0.5px;}
  .course p{margin-top:10px;width:200px;font-size:14px;line-height:18px;font-weight:400;}
  .divider{position:absolute;left:392px;top:622px;width:1.5px;height:186px;background:var(--ink);}
  .benefits{position:absolute;left:447px;top:630px;width:275px;}
  .benefits .lead{font-size:13.5px;font-weight:400;}
  .benefits h3{margin-top:6px;font-weight:700;font-size:28.5px;line-height:36px;letter-spacing:-0.3px;}
  .topics{
    position:absolute;left:73px;top:842px;width:660px;
    font-size:10px;font-weight:700;line-height:17.5px;text-transform:uppercase;
  }
  .footer{position:absolute;left:0;bottom:0;width:786px;height:93px;background:var(--footer);}
</style>
</head>
<body>
  <main class="poster">
    <div class="hero-band"></div>
    <div class="ghost-word top" aria-hidden="true">ARN</div>
    <div class="ghost-word bottom" aria-hidden="true">ARN</div>
    <div class="hero-photo" role="img" aria-label="Photo of a professional man in a white shirt typing on a laptop"></div>

    <h1 class="headline">
      <span class="line learn">LEARN IT</span>
      <span class="joiner">to</span>
      <span class="line earn">EARN IT</span>
    </h1>

    <section class="course">
      <h2>Business Enrichment Course</h2>
      <p>A proven success of helping people in their livelihoods</p>
    </section>

    <div class="divider"></div>

    <section class="benefits">
      <p class="lead">Business skills that will help you:</p>
      <h3>Get a quality job - start / grow your business-Increase your salary</h3>
    </section>

    <p class="topics">
      Business Admiistration – Small Business Management -<br>
      Finance - Investments - Computers- Accounting - Sales &nbsp;Marketing - Project Management Interviewing<br>
      Skills - Business Law -Negotiation – Public Speaking - Import/Export - Information Technoloy -<br>
      Distribution - Marketing - &nbsp;&nbsp;TallyLedger - Real Estate - Health Care-Management - Nimbus Market
    </p>

    <footer class="footer"></footer>
  </main>
</body>
</html>
```